International Trade Consulting Firm Seeks Quality Newsletter Design

Our company provides consulting services to Pinnacle 300 type companies. We compete with the largest consulting companies in the world. However, we have the highest level of expertise in the industry and need to look the most professional and high end. We have very relevant and important information to provide our customers about their compliance and projects. We will have the winning design coded to be an e-newsletter, so it needs to be one page. We want to keep our company colors and logo design in the newsletter, they are attached. We DO NOT want it to look like a mini-version of our website. We want a fresh look to this marketing piece. Newsletter will need to include title, possible sub-heading, space for a feature story, 2 other stories included, and space on either the left or right for short cuts, links or highlights of other articles. Contents/'In this issue' section, about us or branding area, section for relevant links, etc...
Pinnacle 300 companies, High-level management
Marketing

```html
<!DOCTYPE html>
<html lang="en">
<head>
<meta charset="utf-8">
<title>Tradeport Zone Group Newsletter</title>
<link href="https://fonts.googleapis.com/css2?family=Arimo:wght@400;700&family=Roboto+Condensed:wght@400&display=swap" rel="stylesheet">
<style>
  :root {
    --page-green: #266b2d;
    --band-green: #215c27;
    --panel-green: #1f5525;
    --panel-edge: #194a1e;
    --rule-green: #2c7a34;
    --accent: #5fe06b;
    --link: #7cf088;
    --tab-top: #44c852;
    --tab-bottom: #27a236;
    --tab-text: #1c3d1f;
    --header-black: #030403;
    --heading-green: #47b04f;
    --footer-bg: #1d3a22;
    --footer-text: #2f7a35;
    --white: #f4fbf4;
    --notice: #68cf6f;
    --photo-top: #3f8fcf;
    --photo-bottom: #6fb3d8;
  }
  * { box-sizing: border-box; margin: 0; padding: 0; }
  html, body { width: 1200px; height: 1000px; overflow: hidden; }
  body {
    position: relative;
    background: var(--page-green);
    font-family: "Arimo", Arial, sans-serif;
    color: var(--white);
  }
  .abs { position: absolute; }

  .notice-bar {
    left: 0; top: 0; width: 1200px; height: 56px;
    background: var(--band-green);
    border-bottom: 1px solid #1a4a1f;
    text-align: center; font-size: 12px; line-height: 14px;
    color: var(--notice); padding-top: 8px;
  }
  .notice-bar a { color: var(--link); font-weight: 700; }

  .masthead {
    left: 315px; top: 77px; width: 588px; height: 75px;
    background: var(--header-black); border-radius: 8px;
    border: 1px solid #2a6a2f;
  }
  .brand-name {
    left: 14px; top: 26px; font-size: 19px; font-weight: 700;
    color: var(--heading-green); letter-spacing: 0.5px;
  }
  .masthead-title { left: 254px; top: 4px; font-size: 28px; color: var(--heading-green); letter-spacing: 6px; }
  .masthead-sub { left: 262px; top: 46px; font-size: 17px; color: var(--heading-green); letter-spacing: 2px; }

  .panel {
    background: var(--panel-green); border: 1px solid var(--panel-edge);
    border-radius: 6px;
  }
  .feature-panel { left: 318px; top: 193px; width: 366px; height: 645px; }
  .issue-panel { left: 706px; top: 194px; width: 193px; height: 186px; }
  .news-panel { left: 706px; top: 401px; width: 193px; height: 409px; }

  .story-title { font-size: 19px; font-weight: 700; color: var(--accent); }
  .copy { font-size: 13px; line-height: 16px; color: var(--white); }
  .copy a { color: var(--link); }
  .rule { height: 1px; background: var(--rule-green); }

  .bullets { list-style: none; font-size: 13.5px; }
  .bullets li { position: relative; padding-left: 18px; height: 22px; }
  .bullets li::before {
    content: ""; position: absolute; left: 0; top: 5px;
    width: 5px; height: 5px; border-radius: 50%; background: var(--accent);
  }

  .photo {
    left: 340px; top: 392px; width: 323px; height: 175px;
    background: linear-gradient(var(--photo-top), var(--photo-bottom));
    box-shadow: 2px 2px 3px rgba(0,0,0,.5);
  }

  .tab {
    left: 696px; width: 211px; height: 36px; border-radius: 4px 4px 2px 2px;
    background: linear-gradient(var(--tab-top), var(--tab-bottom));
    color: var(--tab-text); font-size: 15px; padding: 7px 0 0 10px;
    box-shadow: 0 3px 2px rgba(0,0,0,.35);
  }
  .tab svg { position: absolute; right: 14px; top: 9px; }

  .side-title { font-size: 13px; font-weight: 700; line-height: 16px; color: var(--accent); }
  .side-copy { font-size: 12.5px; line-height: 15px; color: var(--white); }
  .side-copy a { color: var(--link); }

  .footer {
    left: 0; top: 859px; width: 1200px; height: 141px;
    background: var(--footer-bg); border-top: 1px solid #2d6e33;
  }
  .footer-address {
    left: 0; top: 81px; width: 1200px; text-align: center;
    font-family: "Roboto Condensed", "Arial Narrow", sans-serif;
    font-size: 17px; color: var(--footer-text);
  }
</style>
</head>
<body>
  <div class="abs notice-bar">
    You’re receiving this newsletter because you signed up for it<br>
    Having trouble reading this email? <a href="#">View it in your browser.</a> | <a href="#">Click here to unsubscribe.</a>
  </div>

  <header class="abs masthead">
    <div class="abs brand-name">Tradeport Zone Group</div>
    <div class="abs masthead-title">Heading</div>
    <div class="abs masthead-sub">sub-heading</div>
  </header>

  <main>
    <div class="abs panel feature-panel"></div>
    <h2 class="abs story-title" style="left:340px;top:214px;">Lorem ipsum dolar sit amet</h2>
    <p class="abs copy" style="left:340px;top:246px;width:300px;">Suspendisse potenti--Fusce eu ante in sapien vestibulum sagittis. Cras purus. Nunc rhoncus.</p>
    <p class="abs copy" style="left:340px;top:288px;width:312px;">Donec imperdiet, nibh sit amet pharetra placerat, tortor purus condimentum lectus, at <a href="#">dignissim nibh</a> velit vitae sem. Nunc condimentum blandit phasellus facilisis neque vitae purus.</p>
    <div class="abs rule" style="left:338px;top:372px;width:326px;"></div>

    <div class="abs photo" role="img" aria-label="Feature photo: beach with sea and sky"></div>
    <p class="abs copy" style="left:340px;top:577px;width:300px;">Suspendisse potenti--Fusce eu ante in sapien vestibulum sagittis. Cras purus. Nunc rhoncus.</p>
    <div class="abs rule" style="left:338px;top:627px;width:326px;"></div>

    <h2 class="abs story-title" style="left:340px;top:648px;">Lorem ipsum dolar sit amet</h2>
    <p class="abs copy" style="left:340px;top:680px;width:312px;">Donec imperdiet, nibh sit amet pharetra placerat, tortor purus condimentum lectus, at dignissim nibh velit vitae sem. Nunc condimentum blandit phasellus facilisis neque vitae purus.</p>
    <ul class="abs bullets" style="left:340px;top:753px;">
      <li>Aliquam lectus orci, adipiscing</li>
      <li>Aliquam lectus orci, adipiscing</li>
      <li>Aliquam lectus orci, adipiscing</li>
    </ul>
  </main>

  <aside>
    <div class="abs panel issue-panel"></div>
    <div class="abs tab" style="top:213px;">In this issue
      <svg width="14" height="18" viewBox="0 0 14 18"><circle cx="9" cy="3" r="2" fill="var(--tab-text)"/><path d="M5 7h6l-3 9h2v2H3v-2h2l2.5-7H5z" fill="var(--tab-text)"/></svg>
    </div>
    <ul class="abs bullets" style="left:727px;top:272px;">
      <li>Aliquam lectus orc</li>
      <li>Aliquam lectus orci</li>
      <li>Aliquam lectus orci</li>
      <li>Aliquam lectus orci</li>
    </ul>

    <div class="abs panel news-panel"></div>
    <div class="abs tab" style="top:420px;">In other news
      <svg width="18" height="18" viewBox="0 0 18 18"><circle cx="9" cy="9" r="8" fill="var(--tab-text)"/><path d="M5 5c2 0 3 2 2 4s1 3 0 5M11 3c-1 2 1 3 3 3M12 10c1 1 1 3 0 4" stroke="var(--tab-top)" stroke-width="1.5" fill="none"/></svg>
    </div>
    <h3 class="abs side-title" style="left:727px;top:479px;width:150px;">Lorem ipsum dolar sit amet</h3>
    <p class="abs side-copy" style="left:727px;top:521px;width:142px;">Nunc ipsum metus, iaculis sit amet, interdum at. Donce imperiat ccumsan felis. <a href="#">dignissim nibh</a> Cras sed ante.</p>
    <div class="abs rule" style="left:727px;top:616px;width:152px;"></div>
    <h3 class="abs side-title" style="left:727px;top:636px;width:150px;">Lorem ipsum dolar sit amet</h3>
    <p class="abs side-copy" style="left:727px;top:677px;width:142px;">Nunc ipsum metus, iaculis sit amet, interdum at. Donce imperiat ccumsan felis. <a href="#">dignissim nibh</a> Cras sed ante.</p>
    <div class="abs rule" style="left:727px;top:771px;width:152px;"></div>
  </aside>

  <footer class="abs footer">
    <p class="abs footer-address">Meridian Filings LLC, 1190 North Alder Ave., Suite 310 Denver, CO 80210</p>
  </footer>
</body>
</html>
```